Irrigation Business needs their business cards modernised and revamped

I would like to keep my current logo, colours and revamp the format of the card.

I would like the card to be clean yet important.

Im not sure if you include texture but i would like the named logo to be indented into the card etc.

show me something alive and free something thats clinical to the point yet has a feel of achievement. i would like people to go nice card.

Target Market(s)

high end clients, corporate, sports field manger, the guys that make the decisions

Industry/Entity Type

Business

Contact Information for Business Card

nformation to be included

Dean Harlow (Director)
0487305526
dean@kolvat.biz
www.kestonfieldworks.com

instagram logo
google logo
facebook logo

Colors

Designer to choose colors to be used in the design.

Requirements
Nice to have
• indentations a really nice feel to the card good texture

```html
<!DOCTYPE html>
<html lang="en">
<head>
<meta charset="utf-8">
<title>Keston Fieldworks – Business Card</title>
<link rel="stylesheet" href="https://fonts.googleapis.com/css2?family=Source+Sans+3:wght@400;600;700&display=swap">
<style>
  :root {
    --page-bg: #e9e7e4;
    --card-bg: #f3f4f5;
    --card-edge: #d6d9dc;
    --band-top: #3aa3c4;
    --band-bottom: #1f4f9c;
    --navy: #1c3f7a;
    --green: #2e9a4a;
    --ink: #3b3f44;
    --white: #ffffff;
  }
  * { margin: 0; padding: 0; box-sizing: border-box; }
  html, body {
    width: 1200px; height: 969px; overflow: hidden;
    background: var(--page-bg);
    font-family: "Source Sans 3", Arial, sans-serif;
  }
  .card {
    position: absolute; left: 100px; top: 198px;
    width: 1000px; height: 572px;
    background: linear-gradient(160deg, #f7f8f9 0%, var(--card-bg) 60%, #eceef0 100%);
    border: 1px solid var(--card-edge);
    box-shadow: 0 18px 40px rgba(0,0,0,0.12);
    overflow: hidden;
  }
  .card__band {
    position: absolute; left: 0; top: 0; bottom: 0; width: 132px;
    background: linear-gradient(180deg, var(--band-top) 0%, #2b79b4 45%, var(--band-bottom) 100%);
  }
  .band-mark {
    position: absolute; left: 14px; top: 170px;
    width: 104px; height: 104px; border-radius: 50%;
    border: 4px solid var(--white);
  }
  .contact-icon {
    position: absolute; left: 50px; width: 32px; height: 32px;
  }
  .brand {
    position: absolute; left: 560px; top: 50px; width: 440px;
    text-align: center;
  }
  .brand__dot {
    display: block; margin: 0 auto 18px;
    width: 114px; height: 114px; border-radius: 50%;
    background: linear-gradient(180deg, #2f8fc0, var(--navy));
  }
  .brand__name {
    font-weight: 700; font-size: 40px; color: var(--navy);
    letter-spacing: 0.5px; text-transform: uppercase;
  }
  .person {
    position: absolute; left: 152px; top: 310px;
  }
  .person__name {
    font-weight: 700; font-size: 29px; color: var(--navy);
    text-transform: uppercase; line-height: 1.1;
  }
  .person__role {
    font-weight: 600; font-size: 28px; color: var(--green);
    text-transform: uppercase; line-height: 1.2;
  }
  .contacts {
    position: absolute; left: 152px; top: 408px; list-style: none;
  }
  .contacts li {
    font-size: 25px; color: var(--ink); height: 45px; line-height: 40px;
  }
</style>
</head>
<body>
  <div class="card">
    <div class="card__band">
      <span class="band-mark"></span>

      <svg class="contact-icon" style="top:412px" viewBox="0 0 32 32" aria-hidden="true">
        <circle cx="16" cy="16" r="14" fill="none" stroke="#fff" stroke-width="2"/>
        <path d="M11 9c1 0 2 2 2.5 3s-1 2-1 2.5 2.5 4 4 4.5c.5 0 1.5-1.5 2.5-1s3 1.5 3 2.5-1.5 2.5-3 2.5c-4 0-10-6-10-10 0-2 1-4 2-4z" fill="#fff"/>
      </svg>
      <svg class="contact-icon" style="top:457px" viewBox="0 0 32 32" aria-hidden="true">
        <circle cx="16" cy="16" r="14" fill="none" stroke="#fff" stroke-width="2"/>
        <rect x="9" y="11" width="14" height="10" fill="#fff"/>
        <path d="M9 11l7 6 7-6" fill="none" stroke="#2b79b4" stroke-width="1.5"/>
      </svg>
      <svg class="contact-icon" style="top:502px" viewBox="0 0 32 32" aria-hidden="true">
        <circle cx="16" cy="16" r="14" fill="none" stroke="#fff" stroke-width="2"/>
        <circle cx="16" cy="16" r="7" fill="none" stroke="#fff" stroke-width="1.6"/>
        <path d="M9 16h14M16 9c-3 3-3 11 0 14M16 9c3 3 3 11 0 14" fill="none" stroke="#fff" stroke-width="1.4"/>
      </svg>
    </div>

    <div class="brand">
      <span class="brand__dot"></span>
      <div class="brand__name">Keston Fieldworks</div>
    </div>

    <div class="person">
      <div class="person__name">Dean Harlow</div>
      <div class="person__role">Director</div>
    </div>

    <ul class="contacts">
      <li>0487305526</li>
      <li>dean@kolvat.biz</li>
      <li>kestonfieldworks.com</li>
    </ul>
  </div>
</body>
</html>
```